Business Card Design for ReaL ESTATE AGENT

New Business Cards for a real estate agent in Jacksonville, FL. My specialty is urban core, historic districts but sell through out the city. Company Name is Ninth and Crest Realty a division of the Dunholt Companies. The card needs to convey an essence of professionalism, knowledge and success.

Target Market(s)

Home buyers and Sellers

Industry/Entity Type

Real Estate

Contact Information for Business Card

Double sided

Font styles to use
Sans Serif

Requirements
Must have
• My logs and photo (provided). My contact information as follows:
• Owen Talbrick
• Cell 904-555-0183
• Office 904-555-0147
• Email owentalbrick@mailbrook.example
Nice to have
• Tag Line - Exceptional Effort. Proven Results.

```html
<!DOCTYPE html>
<html lang="en">
<head>
<meta charset="utf-8">
<title>Ninth and Crest Realty – Business Card</title>
<link rel="stylesheet" href="https://fonts.googleapis.com/css2?family=Open+Sans:wght@400;600;700&display=swap">
<style>
  :root {
    --canvas-bg: #e9eaec;
    --card-bg: #ffffff;
    --brand-green: #1f6b45;
    --brand-red: #e5452d;
    --photo-light: #f1efed;
    --photo-mid: #c9c6c3;
    --photo-dark: #2c3138;
  }
  * { box-sizing: border-box; margin: 0; padding: 0; }
  html, body {
    width: 1200px;
    height: 864px;
    overflow: hidden;
  }
  body {
    background: var(--canvas-bg);
    font-family: "Open Sans", Arial, sans-serif;
    position: relative;
  }
  .card {
    position: absolute;
    left: 310px;
    width: 580px;
    height: 322px;
    background: var(--card-bg);
    box-shadow: 0 6px 18px rgba(0,0,0,0.18);
    overflow: hidden;
  }
  .card--back { top: 60px; }
  .card--front { top: 472px; }

  /* Back face: centred brand name and tagline */
  .back-content {
    position: absolute;
    inset: 0;
    display: flex;
    flex-direction: column;
    align-items: center;
    justify-content: center;
    gap: 22px;
  }
  .brand-block {
    display: flex;
    align-items: center;
    gap: 16px;
  }
  .brand-square {
    width: 64px;
    height: 64px;
    border: 5px solid var(--brand-green);
    flex: none;
  }
  .brand-name {
    font-weight: 700;
    font-size: 34px;
    line-height: 1.05;
    color: var(--brand-green);
    letter-spacing: 0.5px;
  }
  .tagline {
    font-size: 14px;
    font-weight: 600;
    color: var(--brand-red);
    letter-spacing: 0.5px;
  }

  /* Front face */
  .front-brand {
    position: absolute;
    left: 30px;
    top: 30px;
    display: flex;
    align-items: center;
    gap: 10px;
  }
  .front-brand .brand-square {
    width: 40px;
    height: 40px;
    border-width: 4px;
  }
  .front-brand .brand-name {
    font-size: 18px;
    line-height: 1.15;
  }
  .agent {
    position: absolute;
    left: 30px;
    top: 150px;
  }
  .agent-name {
    font-weight: 600;
    font-size: 22px;
    color: var(--brand-green);
    line-height: 1.1;
  }
  .agent-title {
    font-size: 13px;
    color: var(--brand-red);
    margin-top: 2px;
  }
  .contact-list {
    position: absolute;
    left: 30px;
    top: 218px;
    list-style: none;
  }
  .contact-item {
    display: flex;
    align-items: center;
    gap: 8px;
    font-size: 13px;
    color: var(--brand-red);
    margin-bottom: 6px;
    white-space: nowrap;
  }
  .contact-label {
    color: var(--brand-green);
    font-weight: 600;
    width: 42px;
  }
  .contact-icon { width: 16px; height: 14px; flex: none; }
  .agent-photo {
    position: absolute;
    right: 0;
    bottom: 0;
    width: 270px;
    height: 322px;
    background: linear-gradient(180deg, var(--photo-light) 0%, var(--photo-mid) 55%, var(--photo-dark) 100%);
  }
</style>
</head>
<body>

<section class="card card--back" aria-label="Card back">
  <div class="back-content">
    <div class="brand-block">
      <div class="brand-square"></div>
      <div class="brand-name">Ninth &amp; Crest<br>Realty</div>
    </div>
    <p class="tagline">Exceptional Effort. Proven Results.</p>
  </div>
</section>

<section class="card card--front" aria-label="Card front">
  <div class="front-brand">
    <div class="brand-square"></div>
    <div class="brand-name">Ninth &amp; Crest<br>Realty</div>
  </div>

  <div class="agent">
    <p class="agent-name">Owen Talbrick</p>
    <p class="agent-title">Managing Director</p>
  </div>

  <ul class="contact-list">
    <li class="contact-item">
      <svg class="contact-icon" viewBox="0 0 16 14" aria-hidden="true">
        <rect x="0.5" y="0.5" width="15" height="13" rx="2" fill="none" stroke="var(--brand-green)"/>
        <path d="M4 4.5c0-1 1-1.5 4-1.5s4 .5 4 1.5v1H10V4.5H6v1H4z M5 7h6l1 4H4z" fill="var(--brand-green)"/>
      </svg>
      <span class="contact-label">Cell</span>
      <span>904-555-0183</span>
    </li>
    <li class="contact-item">
      <svg class="contact-icon" viewBox="0 0 16 14" aria-hidden="true">
        <rect x="0.5" y="0.5" width="15" height="13" rx="2" fill="none" stroke="var(--brand-green)"/>
        <path d="M4 4.5c0-1 1-1.5 4-1.5s4 .5 4 1.5v1H10V4.5H6v1H4z M5 7h6l1 4H4z" fill="var(--brand-green)"/>
      </svg>
      <span class="contact-label">Office</span>
      <span>904-555-0147</span>
    </li>
    <li class="contact-item">
      <svg class="contact-icon" viewBox="0 0 16 14" aria-hidden="true">
        <rect x="0.5" y="0.5" width="15" height="13" rx="2" fill="none" stroke="var(--brand-green)"/>
        <rect x="3" y="4" width="10" height="6.5" fill="none" stroke="var(--brand-green)"/>
        <path d="M3 4l5 4 5-4" fill="none" stroke="var(--brand-green)"/>
      </svg>
      <span>owentalbrick@mailbrook.example</span>
    </li>
  </ul>

  <div class="agent-photo" role="img" aria-label="Portrait photo of the agent in a dark suit and red tie"></div>
</section>

</body>
</html>
```